Design a New Business Card for Our Company

We are looking for fresh, unique, and a modern business card that reflects our roots as digital marketing agency focused on SEM.

Industry/Entity Type

Marketing

Contact Information for Business Card

looking for very unique out of the box designs. clean and modern that compliments our logo

Requirements
Must have
• colors should match our logo
• Front should have name, address, email, and phone/fax of the person, phone/fax are the same number
• back should have our url

```html
<!DOCTYPE html>
<html lang="en">
<head>
<meta charset="utf-8">
<title>Brightwave Solutions – Business Card</title>
<link href="https://fonts.googleapis.com/css2?family=Open+Sans:wght@400;600;700&display=swap" rel="stylesheet">
<style>
  :root {
    --stage: #ececef;
    --card-white: #ffffff;
    --blue-deep: #4a86c6;
    --blue-light: #8fc0ee;
    --brand-blue: #5b97d1;
    --brand-grey: #a9a9ab;
    --text-white: #ffffff;
    --rule: #9cc0e4;
  }
  html, body {
    margin: 0;
    width: 1200px;
    height: 900px;
    overflow: hidden;
    background: var(--stage);
    font-family: "Open Sans", Arial, sans-serif;
  }
  .stage { position: relative; width: 1200px; height: 900px; }

  .card {
    position: absolute;
    height: 342px;
    background: var(--card-white);
    box-shadow: 0 6px 18px rgba(0,0,0,0.12);
    overflow: hidden;
  }

  /* Front */
  .card-front {
    left: 238px; top: 62px; width: 555px;
    background: linear-gradient(90deg, var(--blue-deep) 0%, var(--blue-deep) 42%, var(--blue-light) 60%);
  }
  .front-shape { position: absolute; inset: 0; }
  .holder { position: absolute; left: 31px; top: 50px; color: var(--text-white); }
  .holder-name { margin: 0; font-size: 18px; font-weight: 700; line-height: 22px; }
  .holder-role { margin: 0; font-size: 14.5px; font-weight: 400; line-height: 18px; }
  .address {
    position: absolute; left: 31px; top: 186px;
    margin: 0; color: var(--text-white);
    font-size: 14.5px; line-height: 20px; font-style: normal;
  }
  .contacts {
    position: absolute; left: 31px; top: 240px;
    margin: 0; padding: 0; list-style: none;
    color: var(--text-white); font-size: 14.5px; line-height: 20px;
  }
  .contacts li { display: flex; align-items: center; gap: 8px; }
  .contacts svg { width: 12px; height: 12px; fill: var(--text-white); }

  /* Back */
  .card-back { left: 457px; top: 519px; width: 560px; }
  .brand {
    position: absolute; left: 0; right: 0; top: 124px;
    display: flex; justify-content: center; align-items: center; gap: 14px;
  }
  .brand-dot { width: 30px; height: 30px; border-radius: 50%; background: var(--brand-blue); }
  .brand-name {
    margin: 0; font-size: 44px; font-weight: 600; color: var(--brand-grey);
    letter-spacing: -0.5px; line-height: 1;
  }
  .web {
    position: absolute; left: 0; right: 0; top: 280px;
    display: flex; align-items: center; gap: 14px;
    color: var(--brand-blue); font-size: 15.5px;
  }
  .web::before, .web::after {
    content: ""; flex: 1; height: 1px; background: var(--rule);
  }
</style>
</head>
<body>
<main class="stage">
  <section class="card card-front" aria-label="Business card front">
    <svg class="front-shape" viewBox="0 0 555 342" aria-hidden="true">
      <path d="M555 0 H372 C300 20 300 70 280 110 C262 150 300 190 290 230 C280 270 300 310 330 342 H555 Z" fill="#ffffff"/>
      <circle cx="440" cy="170" r="58" fill="#5b97d1"/>
    </svg>
    <div class="holder">
      <h1 class="holder-name">Marcus Hale</h1>
      <p class="holder-role">Managing Director</p>
    </div>
    <address class="address">12345, Address Goes Here<br>Country Name, 123456.</address>
    <ul class="contacts">
      <li><svg viewBox="0 0 12 12"><path d="M2.4 0.6 L4.2 2.8 L3.2 4.2 C3.8 5.6 5.6 7.6 7.4 8.5 L8.7 7.5 L11 9.3 L9.8 11.2 C5.4 11.2 0.6 6.4 0.6 2 Z"/></svg>044-555 010 220</li>
      <li><svg viewBox="0 0 12 12"><path d="M3 1 H8 V4 H3 Z M1 4.5 H11 V11 H1 Z M3 6.5 H5 V8 H3 Z M6.5 6.5 H9 V8 H6.5 Z" fill-rule="evenodd"/></svg>044-555 010 220</li>
      <li><svg viewBox="0 0 12 12"><path d="M1 2.5 H11 V9.5 H1 Z M1.6 3 L6 6.4 L10.4 3 Z" fill-rule="evenodd"/></svg>info@brightwave.com</li>
    </ul>
  </section>

  <section class="card card-back" aria-label="Business card back">
    <div class="brand">
      <span class="brand-dot" aria-hidden="true"></span>
      <p class="brand-name">Brightwave Solutions</p>
    </div>
    <div class="web">www.brightwave.com</div>
  </section>
</main>
</body>
</html>
```